Computer Company needs a Business card design

We need a business card design for our business. We assist people to transition to the KVS (Kestrel Vantage Scheme). The Verandal Crown Office-owned kvs™ network is a brand new telecommunications network currently being rolled out across Australia, giving access to a reliable broadband connection. Our niche market will predominantly be domestic customers in the 50+ age bracket. The assistance that we provide is everything from arranging the equipment, arranging the plan and contract term, appointment times, final testing of the network and any tweaks that need to be made. We basically PM the transition from start to finish. The business card design should be minimalist, should communicate loyalty and stability, should be easy to read and clearly explain what we do. We have asked for front and back. However, the back of the card does not have to include much information at all. It could be just a small design, or a repeat of our phone number. Up to you. The attached file only says what is required on the card. It does not specify where to arrange the text, what fonts to use, etc etc. As much as we would like to give you more info, due to our very limited design ability, we are not really able to send you any rough, or otherwise, designs of what we are after. Hopefully the above description is enough for you.

```html
<!DOCTYPE html>
<html lang="en">
<head>
<meta charset="utf-8">
<title>kvs Plain Path – Business Card</title>
<link rel="stylesheet" href="https://fonts.googleapis.com/css2?family=Montserrat:wght@600;700&family=Questrial&display=swap">
<style>
  :root {
    --backdrop: #c9c9c9;
    --brand-blue: #0a84ac;
    --name-blue: #1283a8;
    --paper: #f6f6f6;
    --muted: #a8a8a8;
    --ink: #555555;
    --white: #ffffff;
  }
  * { margin: 0; padding: 0; box-sizing: border-box; }
  html, body { width: 1200px; height: 960px; overflow: hidden; }
  body { background: var(--backdrop); position: relative; }

  .card { position: absolute; width: 600px; height: 342px; }

  .card-front {
    left: 321px; top: 108px;
    background: var(--brand-blue);
    display: flex; align-items: center; justify-content: center;
  }
  .brand-name {
    font-family: "Montserrat", sans-serif;
    font-weight: 600;
    font-size: 52px;
    color: var(--white);
    letter-spacing: 0.5px;
    white-space: nowrap;
    transform: translateY(4px);
  }

  .card-back { left: 320px; top: 493px; background: var(--paper); }
  .accent-bar {
    position: absolute; left: 0; top: 198px;
    width: 10px; height: 38px; background: var(--brand-blue);
  }
  .person-name {
    position: absolute; left: 35px; top: 197px;
    font-family: "Montserrat", sans-serif; font-weight: 700;
    font-size: 20px; color: var(--name-blue); letter-spacing: 0.3px;
    white-space: nowrap;
  }
  .person-role {
    position: absolute; left: 35px; top: 223px;
    font-family: "Questrial", sans-serif;
    font-size: 15px; color: var(--muted); letter-spacing: 0.3px;
  }
  .contact-list {
    position: absolute; left: 35px; top: 251px;
    list-style: none;
    font-family: "Questrial", sans-serif;
    font-size: 14px; color: var(--ink); letter-spacing: 0.3px;
  }
  .contact-item { display: flex; align-items: center; height: 19px; white-space: nowrap; }
  .contact-icon { width: 13px; height: 13px; margin-right: 9px; fill: var(--brand-blue); flex: none; }
</style>
</head>
<body>
  <section class="card card-front">
    <span class="brand-name">kvs Plain Path</span>
  </section>

  <section class="card card-back">
    <div class="accent-bar"></div>
    <h1 class="person-name">NEIL ASHCOMBE</h1>
    <p class="person-role">CEO/FOUNDER</p>
    <ul class="contact-list">
      <li class="contact-item">
        <svg class="contact-icon" viewBox="0 0 16 16" aria-hidden="true"><path d="M3.6 1.2l2.2 2.6c.4.4.3 1-.1 1.4L4.6 6.3c.9 2 2.6 3.8 4.8 4.8l1.1-1.1c.4-.4 1-.5 1.4-.1l2.6 2.2c.4.4.4 1 0 1.4l-1.3 1.3c-.6.6-1.6.8-2.4.4C6 13.3 2.7 10 .8 5.2.5 4.4.7 3.4 1.3 2.8l1.3-1.3c.3-.4.7-.4 1-.3z"/></svg>
        <span>0455218903</span>
      </li>
      <li class="contact-item">
        <svg class="contact-icon" viewBox="0 0 16 16" aria-hidden="true"><path d="M1 3.5h14v1L8 9 1 4.5z"/><path d="M1 6l7 4.5L15 6v6.5H1z"/></svg>
        <span>neil@kvsplainpath.com.au</span>
      </li>
      <li class="contact-item">
        <svg class="contact-icon" viewBox="0 0 16 16" aria-hidden="true"><circle cx="8" cy="8" r="7"/><path d="M5 4.5c1 .2 1.8.9 1.6 1.9-.2.8-1.4.8-1.5 1.8 0 1 1 1.3 1 2.3 0 .8-.6 1.4-1 2" fill="none" stroke="#f6f6f6" stroke-width="1.3"/><path d="M10.5 2.8c-.4 1 .3 1.6 1.1 1.9.9.3 1.2 1.2.8 2" fill="none" stroke="#f6f6f6" stroke-width="1.3"/></svg>
        <span>www.kvsplainpath.com.au</span>
      </li>
    </ul>
  </section>
</body>
</html>
```